Core Values Banner For Hearthwell Guards Inc

We want to take the core values for our small growing chimney service company and post them for our entire team to see on a daily basis. We want to be remind everyone how important this is too us all. IntegrityWe try to be honest and accountable in all aspects of our business, as well as in our personal interactions. We do what we say we will do, when we say we will do it, and how we say we will do it.Kaizen“Change for the best”We strive to constantly grow and improve, both personally and professionally. We own up to our mistakes and strive to resolve and learn from them. We actively seek feedback from our clients and each other. We believe the most innovative ideas come when we intentionally look for them.FamilyWe are a family-owned business, and we consider everyone who works here and every one we serve to be part of the family. Being honest and genuine with each other and our customers is what sets us apart. We put ourselves in our customer’s shoes and make recommendations as if it were our chimney, our home and our family.

Font styles to use
Serif
Sans Serif

Colors
ec1f27

Requirements
Must have
• This banner will be approximately 2.5' in height and 6 to 6.5' in width.
• I would like all 3 core values and there definitions listed on the banner
• check out the feel of our marketing on our website www.hearthwellguardsnx.com

```html
<!DOCTYPE html>
<html lang="en">
<head>
<meta charset="utf-8">
<title>Hearthwell Guards Inc — Core Values Banner</title>
<link rel="stylesheet" href="https://fonts.googleapis.com/css2?family=Lato:wght@400;700&display=swap">
<style>
  :root {
    --page-bg: #f2f2f0;
    --panel-red: #c81e39;
    --panel-pink: #d02459;
    --ghost: rgba(255, 255, 255, 0.07);
    --text: #ffffff;
    --shadow: rgba(60, 0, 10, 0.28);
  }
  * { margin: 0; padding: 0; box-sizing: border-box; }
  html, body {
    width: 1200px;
    height: 534px;
    overflow: hidden;
    background: var(--page-bg);
    font-family: "Lato", sans-serif;
    color: var(--text);
  }
  .banner {
    position: absolute;
    left: 30px;
    top: 48px;
    width: 1140px;
    height: 438px;
    display: flex;
    box-shadow: 0 6px 10px rgba(0, 0, 0, 0.22);
    background: var(--panel-red);
  }
  .value {
    position: relative;
    flex: 1 1 0;
    overflow: hidden;
    background: var(--panel-red);
  }
  .value--kaizen {
    background: var(--panel-pink);
    z-index: 1;
    box-shadow: -10px 0 16px -6px var(--shadow), 10px 0 16px -6px var(--shadow);
  }
  .value__ghost {
    position: absolute;
    font-weight: 700;
    font-size: 88px;
    line-height: 1;
    color: var(--ghost);
    white-space: nowrap;
    letter-spacing: 1px;
  }
  .value--integrity .value__ghost { left: 32px; top: 4px; }
  .value--family .value__ghost { right: 30px; top: 4px; }
  .value--kaizen .value__ghost { left: 40px; bottom: -8px; }
  .value__title {
    position: absolute;
    left: 0; right: 0;
    text-align: center;
    font-weight: 400;
    font-size: 45px;
    line-height: 1;
    letter-spacing: 0.5px;
  }
  .value--integrity .value__title,
  .value--family .value__title { top: 84px; }
  .value--kaizen .value__title { top: 66px; }
  .value__tagline {
    position: absolute;
    left: 0; right: 0;
    top: 116px;
    text-align: center;
    font-size: 28px;
    line-height: 1;
  }
  .value__text {
    position: absolute;
    left: 44px;
    right: 44px;
    top: 188px;
    font-size: 16.4px;
    line-height: 26.5px;
    text-align: justify;
    text-align-last: center;
    hyphens: auto;
    -webkit-hyphens: auto;
  }
  .value--kaizen .value__text { top: 186px; }
</style>
</head>
<body>
  <section class="banner" aria-label="Hearthwell Guards Inc core values">
    <article class="value value--integrity">
      <span class="value__ghost" aria-hidden="true">Integrity</span>
      <h2 class="value__title">INTEGRITY</h2>
      <p class="value__text">We try to be honest and accountable in all aspects of our business, as well as in our personal interactions. We do what we say we will do, when we say we will do it, and how we say we will do it.</p>
    </article>
    <article class="value value--kaizen">
      <span class="value__ghost" aria-hidden="true">Kaizen</span>
      <h2 class="value__title">KAIZEN</h2>
      <p class="value__tagline">“Change for the best”</p>
      <p class="value__text">We strive to constantly grow and improve, both personally and professionally. We own up to our mistakes and strive to resolve and learn from them. We actively seek feedback from our clients and each other. We believe the most innovative ideas come when we intentionally look for them.</p>
    </article>
    <article class="value value--family">
      <span class="value__ghost" aria-hidden="true">Family</span>
      <h2 class="value__title">FAMILY</h2>
      <p class="value__text">We are a family-owned business, and we consider everyone who works here and every one we serve to be part of the family. Being honest and genuine with each other and our customers is what sets us apart. We put ourselves in our customer’s shoes and make recommendations as if it were our chimney, our home and our family.</p>
    </article>
  </section>
</body>
</html>
```